Web Design For Marlow Pool Service

We are working with a company that wants a website for their pool service. Some sites to use for content/competitors and inspiration:
https://sacramento.brightwaterpoolco.example/builder/newbuild/repair/ppc
https://hollowbrookpoolcareplus.example/
https://lakemontpoolservice.example/
https://www.dravenspoolresurfacing.example/pool-renovation-ga/
Thank you for taking the time to consider designing a website for us. We are web developers based in Stockton, CA, USA. Most of our projects go through the same process. Understanding this process may help you win a project with us. We custom-code all of our websites in-house. We don’t have any requirements as to what tools you use for your design, but we prefer Figma files. For any design that we label as four-stars, we send it to the client for review. The client picks the final design they want us to use. Once we complete this process, we will continue to show additional clients all the four-star sites and purchase them later. Your designs will have multiple chances to sell. For better chances of success, we ask that you follow these guidelines.
IMAGES:
If you use any images or icons in the design, we ask that you have a link to the asset so we can purchase the image/icon. Most of the designs we submit do not have the customer’s images on them unless they have some great images. Be creative; show us the feeling you are trying to portray with your image choices. Use any royalty-free site you choose. We subscribe to Adobe and mainly use their images, but we can purchase images outside of Adobe. PLEASE NOTE: we will not submit designs to clients with watermarks on the images.
FONTS:
We ask that you identify the fonts used in the design. This can be done in a message if you want. We typically use Google Fonts and Adobe Fonts.
CONTENT:
We're always open to different content and ideas. We often submit designs with stock images so the client can see our vision. We typically take pictures after the website launch to use their images with our vision. Lorem Ipsum is fine for paragraphs, but we ask that you write the headers in correct English. We want to be able to show the vision and identify the sections of the website.
INSPIRATION:
We typically add a couple of links in the brief of websites we like to help you get started in your design.
REVISIONS:
We do not often ask for revisions of the designs unless we see something in the design that may not appeal to the client. If there are slight changes that we want to make, we do that in the development process.
FEEDBACK:
We rarely give feedback on designs during the design process. We are working on many website projects and do not have the time to provide feedback. We usually respond if your request is well thought out and asks specific questions, but a note asking “feedback, please” usually goes unanswered.
Number of Pages Required
1 page
Look and feel
Each slider illustrates characteristics of the customer's brand and the style your logo design should communicate.

```html
<!DOCTYPE html>
<html lang="en">
<head>
<meta charset="utf-8">
<title>Marlow Pool Service</title>
<link href="https://fonts.googleapis.com/css2?family=Merriweather:wght@700;900&family=Montserrat:wght@400;500;600&display=swap" rel="stylesheet">
<style>
:root{
  --blue:#2f9bf0;
  --blue-dark:#1d6fd1;
  --ink:#1b1b1b;
  --text:#333;
  --teal:#2aa3ae;
  --teal-dark:#1f8c98;
  --navy:#163848;
  --footer:#0b0b0b;
  --white:#fff;
  --star:#f5a623;
}
*{box-sizing:border-box;margin:0;padding:0}
html,body{width:1200px;height:4601px;overflow:hidden}
body{position:relative;font-family:"Montserrat",sans-serif;color:var(--text);background:var(--white)}
.abs{position:absolute}
.serif{font-family:"Merriweather",serif}

/* header */
.site-header{position:absolute;top:0;left:0;width:1200px;height:89px;background:var(--white);z-index:5}
.brand{position:absolute;left:98px;top:22px;display:flex;align-items:center;gap:10px}
.brand-mark{width:14px;height:14px;border-radius:50%;background:var(--blue)}
.brand-name{font-family:"Merriweather",serif;font-weight:700;font-size:20px;letter-spacing:1px;color:var(--blue-dark);text-transform:uppercase;line-height:1.1;width:170px}
.nav{position:absolute;top:48px;left:548px;display:flex;gap:32px;font-family:"Merriweather",serif;font-size:14px;color:var(--ink)}
.nav .active{color:var(--blue)}
.nav-contact{position:absolute;left:964px;top:21px;width:138px;height:47px;border-radius:24px;background:var(--blue);color:#fff;font-family:"Merriweather",serif;font-weight:700;font-size:15px;display:flex;align-items:center;justify-content:center;box-shadow:0 3px 6px rgba(0,0,0,.2)}

/* hero */
.hero{position:absolute;top:89px;left:0;width:1200px;height:599px;background:linear-gradient(160deg,#0f63c4 0%,#1d85de 45%,#2c9de9 75%,#1a6cc9 100%)}
.hero-swimmer{position:absolute;left:700px;top:0;width:500px;height:470px;background:radial-gradient(ellipse at 55% 45%,rgba(230,120,160,.35),rgba(40,140,230,0) 60%)}
.hero h1{position:absolute;left:98px;top:150px;font-family:"Merriweather",serif;font-weight:900;font-size:46px;line-height:68px;color:#fff;letter-spacing:.5px}
.hero p{position:absolute;left:98px;top:290px;width:520px;font-size:15px;line-height:31px;color:#fff}
.btn-outline{position:absolute;height:46px;border:2px solid #fff;border-radius:24px;color:#fff;font-family:"Merriweather",serif;font-weight:700;font-size:14px;display:flex;align-items:center;justify-content:center}
.btn-fill-white{background:#fff;color:var(--blue)}
.torn{position:absolute;left:0;width:1200px}

/* who we are */
.who h2{position:absolute;left:98px;top:822px;font-family:"Merriweather",serif;font-weight:900;font-size:32px;color:var(--ink)}
.who h3{position:absolute;left:98px;top:882px;font-weight:600;font-size:21px;color:var(--blue)}
.who p{position:absolute;left:98px;top:920px;width:470px;font-size:15px;line-height:31px;color:var(--text)}
.btn-blue{position:absolute;background:var(--blue);color:#fff;border-radius:24px;font-family:"Merriweather",serif;font-weight:700;font-size:15px;display:flex;align-items:center;justify-content:center;box-shadow:0 3px 6px rgba(0,0,0,.2)}
.who-shape{position:absolute;left:700px;top:765px;width:360px;height:450px;background:#dff0fc;transform:skewY(-8deg)}
.who-frame{position:absolute;left:650px;top:793px;width:428px;height:406px;border:2px solid var(--blue)}
.who-photo{position:absolute;left:634px;top:807px;width:429px;height:407px;background:linear-gradient(180deg,#5a7a4a 0%,#8ca48b 35%,#d9dcd4 52%,#4fb3c5 70%,#2b9aac 100%)}

/* what we do */
.services-band{position:absolute;top:1357px;left:0;width:1200px;height:800px;background:linear-gradient(180deg,#32aab4,#2399a6 60%,#2aa3ae)}
.services-band h2{position:absolute;top:1465px;left:0;width:1200px;text-align:center;font-family:"Merriweather",serif;font-weight:900;font-size:32px;color:#fff}
.grid{position:absolute;left:98px;top:1538px;width:1000px;height:428px;display:grid;grid-template-columns:333px 334px 333px;grid-template-rows:214px 214px}
.cell-text{background:#fff;text-align:center;padding-top:38px}
.cell-text h3{font-family:"Merriweather",serif;font-weight:700;font-size:20px;color:var(--ink);margin-bottom:14px}
.cell-text p{font-size:14px;line-height:31px;color:var(--text);padding:0 24px}
.cell-text a{display:inline-block;margin-top:10px;font-weight:600;font-size:15px;color:var(--blue);text-decoration:underline}
.ph-pool-tile{background:linear-gradient(180deg,#a9c9db 0%,#e8f2f5 28%,#4ea9dc 45%,#1b7bc8 100%)}
.ph-tech{background:linear-gradient(150deg,#3e7aa4 0%,#2f8fcf 40%,#1f1f24 70%,#3b78b8 100%)}
.ph-aerial{background:linear-gradient(120deg,#1560c0 0%,#2b8ae0 50%,#d7b88e 75%,#e7d3b6 100%)}
.btn-white{position:absolute;background:#fff;color:var(--blue);border-radius:24px;font-family:"Merriweather",serif;font-weight:700;font-size:15px;display:flex;align-items:center;justify-content:center;box-shadow:0 3px 6px rgba(0,0,0,.2)}

/* products */
.products h2{position:absolute;top:2248px;left:0;width:1200px;text-align:center;font-family:"Merriweather",serif;font-weight:900;font-size:32px;color:var(--ink)}
.products .lead{position:absolute;top:2310px;left:160px;width:880px;text-align:center;font-size:15px;line-height:31px}
.product-img{position:absolute;top:2400px;height:286px;width:318px;border-radius:12px}
.product-label{position:absolute;top:2712px;width:318px;text-align:center;font-family:"Merriweather",serif;font-weight:700;font-size:20px;color:var(--ink)}
.ph-beach{background:linear-gradient(180deg,#4ca6e8 0%,#bfe2f5 40%,#36c1d8 65%,#d8c6a8 100%)}
.ph-garden{background:linear-gradient(180deg,#2c4a26 0%,#4d7a3c 45%,#46d0e0 65%,#9b8a7c 100%)}
.ph-gear{background:linear-gradient(180deg,#49a5e6 0%,#1f6fd1 55%,#0f4fa8 100%)}

/* gallery */
.gallery-band{position:absolute;top:2911px;left:0;width:1200px;height:680px;background:linear-gradient(180deg,#1b4558,#123243 55%,#1a4456)}
.gallery-band h2{position:absolute;top:3012px;left:0;width:1200px;text-align:center;font-family:"Merriweather",serif;font-weight:900;font-size:34px;color:#fff}
.gal{position:absolute;border-radius:14px}
.ph-rock{background:linear-gradient(180deg,#c98b4a 0%,#7d6a3c 35%,#8e8175 55%,#3aa0c8 80%,#1f6fa8 100%)}
.ph-sunset{background:linear-gradient(180deg,#e9a3a0 0%,#8b9a6a 40%,#2f8fd6 75%,#1b66b5 100%)}
.ph-water{background:linear-gradient(135deg,#3ec5ea,#1a9ad8 60%,#52d0f0)}
.ph-freeform{background:linear-gradient(180deg,#3f4a3a 0%,#6c7a70 35%,#2a7fd3 65%,#1a4fb0 100%)}
.ph-lane{background:linear-gradient(180deg,#8ac8ee,#3c93d6 60%,#1e6bb8)}

/* testimonials */
.testimonials h2{position:absolute;top:3690px;left:0;width:1200px;text-align:center;font-family:"Merriweather",serif;font-weight:900;font-size:34px;color:var(--ink)}
.t-card{position:absolute;top:3772px;width:468px;height:270px;background:#fff;box-shadow:0 2px 14px rgba(0,0,0,.15)}
.t-avatar{position:absolute;left:24px;top:30px;width:100px;height:100px;border-radius:50%;background:linear-gradient(180deg,#7fb6e0,#2d5f8a)}
.t-name{position:absolute;left:148px;top:42px;font-weight:500;font-size:18px;color:var(--ink)}
.t-role{position:absolute;left:148px;top:72px;font-size:14px;color:var(--text)}
.t-stars{position:absolute;left:285px;top:70px;font-size:13px;letter-spacing:1px;color:var(--star)}
.t-badge{position:absolute;right:34px;top:40px;width:26px;height:26px;border-radius:50%;background:#e3e8ee}
.t-quote{position:absolute;left:28px;top:140px;font-family:"Merriweather",serif;font-size:110px;line-height:1;color:#b8d8f4}
.t-text{position:absolute;left:150px;top:96px;width:290px;font-size:16px;line-height:30px;color:var(--ink)}
.t-text span{color:var(--blue);font-size:12px}
.t-corner{position:absolute;right:0;bottom:0;width:20px;height:18px;background:#9ccff5}
.arrow-circle{position:absolute;width:34px;height:34px;border:1.5px solid #555;border-radius:50%}
.arrow-circle.blue{border-color:var(--blue)}

/* footer */
.site-footer{position:absolute;top:4143px;left:0;width:1200px;height:458px;background:var(--footer);color:#fff}
.f-brand{position:absolute;left:98px;top:118px;display:flex;align-items:center;gap:10px}
.f-brand .brand-name{color:var(--blue);font-size:22px;width:200px}
.socials{position:absolute;left:98px;top:222px;display:flex;gap:14px}
.socials span{width:38px;height:34px;background:var(--blue)}
.f-col h4{position:absolute;font-family:"Merriweather",serif;font-weight:700;font-size:20px;color:#fff}
.f-rule{position:absolute;width:34px;height:2px;background:#fff}
.f-menu{position:absolute;left:387px;top:122px;list-style:none;font-size:14px;line-height:31px}
.f-contact{position:absolute;left:538px;top:114px}
.f-contact .row{display:flex;align-items:center;gap:14px;height:38px;margin-bottom:22px;font-size:15px}
.f-contact .ico{width:38px;height:38px;border-radius:50%;background:var(--blue);display:flex;align-items:center;justify-content:center}
.f-sign p{position:absolute;left:843px;top:122px;width:260px;font-size:14px;line-height:31px}
.f-input{position:absolute;left:843px;top:209px;width:259px;height:43px;background:#fff;font-size:11px;color:#999;padding:14px 14px}
.f-send{position:absolute;left:843px;top:268px;width:259px;height:45px;background:var(--blue);color:#fff;font-size:17px;font-weight:500;display:flex;align-items:center;justify-content:center}
.f-divider{position:absolute;left:98px;top:398px;width:1004px;height:1px;background:#444}
.copyright{position:absolute;top:418px;left:0;width:1200px;text-align:center;font-size:14px;color:#fff}
</style>
</head>
<body>

<header class="site-header">
  <div class="brand"><span class="brand-mark"></span><span class="brand-name">Marlow<br>Pool Service</span></div>
  <nav class="nav"><span class="active">HOME</span><span>SERVICES</span><span>PRODUCTS</span><span>ABOUT US</span></nav>
  <div class="nav-contact">Contact Us</div>
</header>

<section class="hero" role="img" aria-label="Underwater photo of a child swimming in a bright blue pool">
  <div class="hero-swimmer"></div>
  <h1>WELCOME TO<br>MARLOW POOL SERVICE</h1>
  <p>Lorem ipsum dolor sit amet, consectetur adipiscing elit, sed do eiusmod tempor incididunt ut labore et dolore magna aliqua.</p>
  <div class="btn-outline btn-fill-white" style="left:96px;top:370px;width:209px">GET A FREE QUOTE</div>
  <div class="btn-outline" style="left:320px;top:370px;width:210px">SERVICE REQUEST</div>
</section>
<svg class="torn" style="top:650px" width="1200" height="42" viewBox="0 0 1200 42"><path d="M0 20 L30 14 L55 22 L90 12 L120 20 L160 10 L200 18 L240 12 L280 22 L330 14 L370 20 L410 12 L460 22 L500 14 L550 20 L600 10 L640 18 L690 12 L730 22 L780 14 L820 20 L870 10 L910 18 L960 12 L1000 22 L1050 14 L1090 20 L1140 12 L1200 18 L1200 42 L0 42 Z" fill="#fff"/></svg>

<section class="who">
  <h2>Who We Are</h2>
  <h3>Pool Repairs and Marlow Pool Service</h3>
  <p>Lorem ipsum dolor sit amet, consectetur adipiscing elit, sed do eiusmod tempor incididunt ut labore et dolore magna aliqua. Ut enim ad minim veniam, quis nostrud exercitation ullamco laboris nisi ut aliquip ex ea commodo consequat. Duis aute irure dolor in reprehenderit in voluptate velit esse cillum dolore eu fugiat nulla pariatur. Excepteur sint occaecat cupidatat non proident, sunt in culpa qui officia deserunt mollit anim id est laborum.</p>
  <div class="btn-blue" style="left:98px;top:1189px;width:138px;height:46px">Read More</div>
  <div class="who-shape"></div>
  <div class="who-frame"></div>
  <div class="who-photo" role="img" aria-label="House with a curved backyard pool and spa among palm trees"></div>
</section>

<section class="services-band">
</section>
<svg class="torn" style="top:1350px" width="1200" height="140" viewBox="0 0 1200 140"><path d="M0 0 H1200 V140 Q600 -20 0 140 Z" fill="#fff"/><path d="M75 100 Q600 -25 1130 100 Q600 -5 75 100 Z" fill="#2f9bf0"/></svg>
<h2 class="abs serif" style="top:1465px;left:0;width:1200px;text-align:center;font-weight:900;font-size:32px;color:#fff">What We Do</h2>
<div class="grid">
  <div class="ph-pool-tile" role="img" aria-label="Clean tiled pool edge"></div>
  <div class="cell-text"><h3>Pool Cleaning Service</h3><p>Lorem ipsum dolor sit amet, eiusmod tempor incididunt ut magna aliqua.</p><a>Learn More</a></div>
  <div class="ph-tech" role="img" aria-label="Technician fitting a robotic pool cleaner"></div>
  <div class="cell-text"><h3>Swimming Pool Services</h3><p>Lorem ipsum dolor sit amet, eiusmod tempor incididunt ut magna aliqua.</p><a>Learn More</a></div>
  <div class="ph-aerial" role="img" aria-label="Aerial view of a pool being vacuumed"></div>
  <div class="cell-text"><h3>Swimming Pool Repair</h3><p>Lorem ipsum dolor sit amet, eiusmod tempor incididunt ut magna aliqua.</p><a>Learn More</a></div>
</div>
<div class="btn-white" style="left:498px;top:2013px;width:204px;height:46px">View More Services</div>
<svg class="torn" style="top:2125px" width="1200" height="36" viewBox="0 0 1200 36"><path d="M0 10 L40 18 L80 8 L130 16 L170 6 L220 16 L260 8 L310 18 L350 8 L400 16 L450 6 L500 18 L540 8 L590 16 L640 6 L690 18 L730 8 L780 16 L830 6 L880 18 L920 8 L970 16 L1020 6 L1070 18 L1110 8 L1160 16 L1200 8 L1200 36 L0 36 Z" fill="#fff"/></svg>

<section class="products">
  <h2>Our Products</h2>
  <p class="lead">Lorem ipsum dolor sit amet, consectetur adipiscing elit, sed do eiusmod tempor incididunt ut labore et dolore magna aliqua.</p>
  <svg class="abs" style="left:40px;top:2554px" width="16" height="28" viewBox="0 0 16 28"><path d="M14 2 L3 14 L14 26" fill="none" stroke="#888" stroke-width="2"/></svg>
  <svg class="abs" style="left:1140px;top:2554px" width="16" height="28" viewBox="0 0 16 28"><path d="M2 2 L13 14 L2 26" fill="none" stroke="#222" stroke-width="2"/></svg>
  <div class="product-img ph-beach" style="left:98px" role="img" aria-label="Resort pool with loungers and palms by the beach"></div>
  <div class="product-img ph-garden" style="left:441px" role="img" aria-label="Rectangular pool in a green garden"></div>
  <div class="product-img ph-gear" style="left:782px" role="img" aria-label="Pool vacuum head and blue hose"></div>
  <div class="product-label" style="left:98px">Spas</div>
  <div class="product-label" style="left:441px">Above Ground Pools</div>
  <div class="product-label" style="left:782px">Equipment</div>
</section>

<section class="gallery-band" role="img" aria-label="Dark rippling pool water background"></section>
<svg class="torn" style="top:2905px" width="1200" height="30" viewBox="0 0 1200 30"><path d="M0 0 H1200 V14 L1160 8 L1110 18 L1060 8 L1010 16 L960 6 L910 16 L860 8 L810 18 L760 8 L710 16 L660 6 L610 16 L560 8 L510 18 L460 8 L410 16 L360 6 L310 16 L260 8 L210 18 L160 8 L110 16 L60 6 L0 14 Z" fill="#fff"/></svg>
<svg class="torn" style="top:3565px" width="1200" height="30" viewBox="0 0 1200 30"><path d="M0 16 L50 8 L100 18 L150 8 L200 16 L250 6 L300 18 L350 8 L400 16 L450 6 L500 18 L550 8 L600 16 L650 6 L700 18 L750 8 L800 16 L850 6 L900 18 L950 8 L1000 16 L1050 6 L1100 18 L1150 8 L1200 14 V30 H0 Z" fill="#fff"/></svg>
<h2 class="abs serif" style="top:3012px;left:0;width:1200px;text-align:center;font-weight:900;font-size:34px;color:#fff">Gallery</h2>
<div class="gal ph-rock" style="left:98px;top:3120px;width:486px;height:336px" role="img" aria-label="Rock grotto pool with a white gazebo"></div>
<div class="gal ph-sunset" style="left:602px;top:3120px;width:241px;height:157px" role="img" aria-label="Backyard pool with waterfall at sunset"></div>
<div class="gal ph-water" style="left:859px;top:3120px;width:241px;height:157px" role="img" aria-label="Sparkling pool water surface"></div>
<div class="gal ph-freeform" style="left:602px;top:3295px;width:241px;height:161px" role="img" aria-label="Freeform pool with stone deck"></div>
<div class="gal ph-lane" style="left:859px;top:3295px;width:241px;height:161px" role="img" aria-label="Underwater view of pool lanes"></div>

<section class="testimonials">
  <h2>Client Testimonials</h2>
  <svg class="arrow-circle" style="left:33px;top:3885px" viewBox="0 0 34 34"><path d="M19 10 L12 17 L19 24" fill="none" stroke="#555" stroke-width="2"/></svg>
  <svg class="arrow-circle blue" style="left:1128px;top:3885px" viewBox="0 0 34 34"><path d="M15 10 L22 17 L15 24" fill="none" stroke="#2f9bf0" stroke-width="2"/></svg>
  <article class="t-card" style="left:109px">
    <div class="t-avatar" role="img" aria-label="Client portrait"></div>
    <div class="t-name">Dana Whitfield</div><div class="t-role">Lorem Ipsum set</div><div class="t-stars">★★★★★</div>
    <div class="t-badge"></div>
    <div class="t-quote">“</div>
    <p class="t-text">Nemo enim ipsam voluptatem quia voluptas sit aspernatur aut odit aut fugit, sed quia consequuntur magni dolores eos qui ratione voluptatem sequi nesciunt <span>»</span></p>
    <div class="t-corner"></div>
  </article>
  <article class="t-card" style="left:618px">
    <div class="t-avatar" role="img" aria-label="Client portrait"></div>
    <div class="t-name">Dana Whitfield</div><div class="t-role">Lorem Ipsum set</div><div class="t-stars">★★★★★</div>
    <div class="t-badge"></div>
    <div class="t-quote">“</div>
    <p class="t-text">Nemo enim ipsam voluptatem quia voluptas sit aspernatur aut odit aut fugit, sed quia consequuntur magni dolores eos qui ratione voluptatem sequi nesciunt <span>»</span></p>
    <div class="t-corner"></div>
  </article>
</section>

<footer class="site-footer">
  <div class="f-brand"><span class="brand-mark"></span><span class="brand-name">Marlow<br>Pool Service</span></div>
  <div class="socials"><span></span><span></span><span></span></div>
  <div class="f-col">
    <h4 style="left:384px;top:80px">Menu</h4><div class="f-rule" style="left:384px;top:112px"></div>
    <ul class="f-menu"><li>Home</li><li>Services</li><li>Products</li><li>About Us</li><li>Contact Us</li></ul>
  </div>
  <div class="f-col">
    <h4 style="left:538px;top:80px">Contact Us</h4><div class="f-rule" style="left:538px;top:112px"></div>
    <div class="f-contact" style="top:130px">
      <div class="row"><span class="ico"><svg width="14" height="18" viewBox="0 0 14 18"><path d="M7 1a6 6 0 0 1 6 6c0 4-6 10-6 10S1 11 1 7a6 6 0 0 1 6-6z" fill="#fff"/><circle cx="7" cy="7" r="2" fill="#2f9bf0"/></svg></span>Company Name,United State.</div>
      <div class="row"><span class="ico"><svg width="16" height="12" viewBox="0 0 16 12"><rect width="16" height="12" rx="1" fill="#fff"/><path d="M1 1 L8 7 L15 1" fill="none" stroke="#2f9bf0" stroke-width="1.5"/></svg></span>info@marlowpool.example</div>
      <div class="row"><span class="ico"><svg width="16" height="16" viewBox="0 0 16 16"><path d="M3 1 L6 1 L7 5 L5 6 Q6 9 10 11 L11 9 L15 10 L15 13 Q14 15 12 15 Q1 13 1 3 Q1 1 3 1 Z" fill="#fff"/></svg></span>+1 555 0100 2200</div>
    </div>
  </div>
  <div class="f-col f-sign">
    <h4 style="left:838px;top:80px">Sign Up For Email</h4><div class="f-rule" style="left:843px;top:112px"></div>
    <p>Subscribe us for more information on our solutions and services</p>
  </div>
  <div class="f-input">Email Address</div>
  <div class="f-send">Send</div>
  <div class="f-divider"></div>
  <div class="copyright">Copyrights@2024.Marlow Pool Service.All Rights Reserved</div>
</footer>

</body>
</html>
```